Business card

We need a business card design for our company based in Auckland , New Zealand called 'Ridge + Studio Ltd'. We provide architectural services. We would like to see designs that use the max. three colours (such as white, black, grey) The final design should communicate financial safety and growth."
Also I will provide our company logo. I would like to the logo to be embeded onto our business card.

Target Market(s)

new residential house, alteration & addition & light commericila design & drafting service

Industry/Entity Type

Architecture

Contact Information for Business Card

Company name: ridge + studio Ltd.
Name: Mark Delford
Job title: architectural designer & Design LBP
email address: mark@rplusd.co.nz
mobile number: 02 5163 2290
web site: www.rplusd.co.nz

Requirements
Must have
• My project must have..
• - embeded logo (attached company logo)
• I don't have a bigger version for our company logo, but I have one old one, so you can remove the word from it)
• - insert the attached small BKTW logo & LBP logo
• - creative, simple and clear business card.
• - Max. three colours
Nice to have
• - Here are the samples I would like to share with you: http://www.plimvora.com/blog/minimalistic-business-card-designs/
• I would like to have my business card like one of the creation.
Should not have
• TBA

```html
<!DOCTYPE html>
<html lang="en">
<head>
<meta charset="utf-8">
<title>Ridge + Studio Ltd — Business Card</title>
<link href="https://fonts.googleapis.com/css2?family=Roboto+Condensed:wght@300;400&display=swap" rel="stylesheet">
<style>
  :root {
    --backdrop: #4a4a4a;
    --card-white: #ffffff;
    --card-dark: #3f3f3f;
    --accent: #f7941d;
    --ink: #2b2b2b;
    --faint: #e8e8e8;
    --badge: #2f2f2f;
  }
  html, body {
    margin: 0;
    padding: 0;
    width: 1200px;
    height: 1200px;
    overflow: hidden;
    background: var(--backdrop);
    font-family: "Roboto Condensed", sans-serif;
  }
  .canvas {
    position: relative;
    width: 1200px;
    height: 1200px;
  }
  .card {
    position: absolute;
    left: 282px;
    width: 638px;
    height: 362px;
    box-shadow: 0 4px 10px rgba(0,0,0,0.35);
    overflow: hidden;
  }
  .card-front { top: 222px; background: var(--card-white); }
  .card-back  { top: 646px; background: var(--card-dark); }

  .brand-watermark {
    position: absolute;
    right: 22px;
    top: 40px;
    font-weight: 300;
    font-size: 44px;
    color: var(--faint);
    letter-spacing: 0.5px;
    margin: 0;
  }
  .person-name {
    position: absolute;
    left: 27px;
    top: 178px;
    margin: 0;
    font-weight: 300;
    font-size: 31px;
    line-height: 1;
    color: var(--accent);
  }
  .person-title {
    position: absolute;
    left: 27px;
    top: 214px;
    margin: 0;
    font-weight: 300;
    font-size: 19px;
    line-height: 1;
    color: var(--ink);
  }
  .divider {
    position: absolute;
    left: 27px;
    top: 250px;
    width: 579px;
    height: 1px;
    background: var(--accent);
  }
  .contact-list {
    position: absolute;
    left: 27px;
    top: 270px;
    margin: 0;
    padding: 0;
    list-style: none;
  }
  .contact-list li {
    display: flex;
    align-items: center;
    height: 24px;
    font-weight: 300;
    font-size: 19px;
    color: var(--ink);
  }
  .contact-list svg {
    width: 16px;
    height: 16px;
    margin-right: 18px;
    flex: none;
  }
  .badge-lbp {
    position: absolute;
    left: 454px;
    top: 265px;
    width: 68px;
    height: 68px;
    border-radius: 50%;
    background: var(--badge);
  }
  .badge-bktw {
    position: absolute;
    left: 540px;
    top: 274px;
    width: 44px;
    height: 44px;
    background: #8a8a8a;
  }
  .back-brand {
    position: absolute;
    left: 0;
    right: 0;
    top: 163px;
    display: flex;
    justify-content: center;
    align-items: center;
    gap: 12px;
  }
  .back-brand .dot {
    width: 14px;
    height: 14px;
    border-radius: 50%;
    background: var(--accent);
  }
  .back-brand .name {
    font-weight: 300;
    font-size: 30px;
    color: var(--accent);
    line-height: 1;
  }
</style>
</head>
<body>
<div class="canvas">

  <section class="card card-front">
    <p class="brand-watermark">ridge + studio</p>
    <h1 class="person-name">Mark Delford</h1>
    <p class="person-title">architectural designer &amp; Design LBP</p>
    <div class="divider"></div>
    <ul class="contact-list">
      <li>
        <svg viewBox="0 0 16 16" aria-hidden="true">
          <rect x="1" y="3" width="14" height="10" fill="var(--accent)"/>
          <path d="M1 3 L8 9 L15 3" fill="none" stroke="#fff" stroke-width="1.2"/>
        </svg>
        mark@rplusd.co.nz
      </li>
      <li>
        <svg viewBox="0 0 16 16" aria-hidden="true">
          <rect x="3.5" y="0.8" width="9" height="14.4" rx="1.6" fill="none" stroke="var(--accent)" stroke-width="1.4"/>
          <line x1="3.5" y1="12" x2="12.5" y2="12" stroke="var(--accent)" stroke-width="1"/>
        </svg>
        02 5163 2290
      </li>
      <li>
        <svg viewBox="0 0 16 16" aria-hidden="true">
          <circle cx="8" cy="8" r="6.8" fill="none" stroke="var(--accent)" stroke-width="1.2"/>
          <ellipse cx="8" cy="8" rx="3" ry="6.8" fill="none" stroke="var(--accent)" stroke-width="1"/>
          <line x1="1.2" y1="8" x2="14.8" y2="8" stroke="var(--accent)" stroke-width="1"/>
          <line x1="2.5" y1="4.5" x2="13.5" y2="4.5" stroke="var(--accent)" stroke-width="0.9"/>
          <line x1="2.5" y1="11.5" x2="13.5" y2="11.5" stroke="var(--accent)" stroke-width="0.9"/>
        </svg>
        www.rplusd.co.nz
      </li>
    </ul>
    <div class="badge-lbp" role="img" aria-label="Licensed building practitioner badge"></div>
    <div class="badge-bktw" role="img" aria-label="BKTW professional member badge"></div>
  </section>

  <section class="card card-back">
    <div class="back-brand">
      <span class="dot"></span>
      <span class="name">ridge + studio</span>
    </div>
  </section>

</div>
</body>
</html>
```